Open Door Stays

We are 100% online, promoting accommodation details and booking facilities for wheelchair dependant travellers.
Listings will only be accommodation providers which meet our specific criteria.

Target Market(s)

Wheelchair dependant people and their companions

Industry/Entity Type

Accommodation

Contact Information for Business Card

Name, mobile phone number, email address, website address

```html
<!DOCTYPE html>
<html lang="en">
<head>
<meta charset="utf-8">
<title>Open Door Stays – Business Card</title>
<link rel="stylesheet" href="https://fonts.googleapis.com/css2?family=Exo+2:wght@400;500;600&display=swap">
<style>
  :root {
    --backdrop: #3b3b3d;
    --card: #ffffff;
    --brand-blue: #00aeef;
    --frame-grey: #6d6e71;
    --band-grey: #b5b6b8;
    --soft-grey: #c4c5c7;
    --ink: #2a2a2c;
    --muted: #7a7b7e;
    --on-blue: #ffffff;
  }
  * { margin: 0; padding: 0; box-sizing: border-box; }
  html, body {
    width: 1200px; height: 819px; overflow: hidden;
    background: var(--backdrop);
    font-family: "Exo 2", sans-serif;
  }
  .card {
    position: absolute; left: 100px; top: 123px;
    width: 1000px; height: 572px;
    background: var(--card);
    overflow: hidden;
    box-shadow: 0 18px 40px rgba(0,0,0,.35);
  }
  .card-shapes { position: absolute; inset: 0; }
  .brand { position: absolute; left: 430px; top: 140px; }
  .brand-name {
    color: var(--brand-blue); font-size: 46px; font-weight: 500;
    letter-spacing: 6px; text-transform: uppercase; white-space: nowrap;
  }
  .brand-tagline {
    color: var(--muted); font-size: 18px; letter-spacing: 3.5px;
    text-transform: uppercase; margin-top: 6px; white-space: nowrap;
  }
  .holder { position: absolute; left: 36px; top: 214px; }
  .holder-name {
    color: var(--ink); font-size: 38px; font-weight: 500;
    letter-spacing: 3px; text-transform: uppercase; white-space: nowrap;
  }
  .holder-rule { width: 150px; height: 6px; background: var(--brand-blue); margin: 6px 0 8px; }
  .holder-role {
    color: var(--on-blue); font-size: 19px; letter-spacing: 3px; text-transform: uppercase;
  }
  .contact {
    position: absolute; display: flex; align-items: center; gap: 12px;
    font-size: 19px; letter-spacing: 1px; white-space: nowrap;
  }
  .contact svg { width: 20px; height: 20px; flex: none; }
  .contact--dark { color: var(--ink); }
  .contact--dark svg { fill: var(--brand-blue); }
  .contact--light { color: var(--on-blue); }
  .contact--light svg { fill: var(--on-blue); }
  .address { align-items: flex-start; line-height: 1.4; font-size: 21px; }
  .address svg { margin-top: 4px; width: 22px; height: 22px; }
</style>
</head>
<body>
  <div class="card">
    <svg class="card-shapes" viewBox="0 0 1000 572" width="1000" height="572" aria-hidden="true">
      <polygon points="0,0 250,0 250,572 0,572" fill="var(--brand-blue)"/>
      <rect x="250" y="400" width="750" height="115" fill="var(--brand-blue)"/>
      <rect x="0" y="530" width="1000" height="42" fill="var(--soft-grey)"/>
      <polyline points="340,-20 292,150 292,300 365,340 1020,340"
                fill="none" stroke="var(--frame-grey)" stroke-width="24" stroke-linejoin="miter"/>
      <polygon points="0,198 395,198 362,330 0,330" fill="var(--band-grey)"/>
      <polygon points="645,400 675,400 640,515 610,515" fill="var(--soft-grey)"/>
      <polygon points="640,530 670,530 657,572 627,572" fill="var(--frame-grey)"/>
    </svg>

    <div class="brand">
      <div class="brand-name">Open Door Stays</div>
      <div class="brand-tagline">Accessible Accommodation</div>
    </div>

    <div class="holder">
      <div class="holder-name">Maya Fenwick</div>
      <div class="holder-rule"></div>
      <div class="holder-role">General Manager</div>
    </div>

    <div class="contact contact--dark" style="left:318px; top:363px;">
      <svg viewBox="0 0 20 20"><path d="M10 0a10 10 0 1 0 0 20 10 10 0 0 0 0-20zm6.9 6h-3a14 14 0 0 0-1.2-4A8 8 0 0 1 16.9 6zM10 2c.8 1.1 1.5 2.5 1.9 4H8.1C8.5 4.5 9.2 3.1 10 2zM2.3 12a8 8 0 0 1 0-4h3.4a15 15 0 0 0 0 4H2.3zm.8 2h3a14 14 0 0 0 1.2 4A8 8 0 0 1 3.1 14zm3-8h-3a8 8 0 0 1 4.2-4 14 14 0 0 0-1.2 4zM10 18c-.8-1.1-1.5-2.5-1.9-4h3.8c-.4 1.5-1.1 2.9-1.9 4zm2.3-6H7.7a13 13 0 0 1 0-4h4.6a13 13 0 0 1 0 4zm.4 6a14 14 0 0 0 1.2-4h3a8 8 0 0 1-4.2 4zm1.6-6a15 15 0 0 0 0-4h3.4a8 8 0 0 1 0 4h-3.4z"/></svg>
      <span>www.opendoorstays.example</span>
    </div>
    <div class="contact contact--dark" style="left:660px; top:363px;">
      <svg viewBox="0 0 20 20"><path d="M1 4h18v12H1z M1 4l9 7 9-7" fill="none" stroke="var(--brand-blue)" stroke-width="2"/></svg>
      <span>maya@opendoorstays.example</span>
    </div>

    <div class="contact contact--light address" style="left:290px; top:418px;">
      <svg viewBox="0 0 20 20"><path d="M10 0a7 7 0 0 0-7 7c0 5 7 13 7 13s7-8 7-13a7 7 0 0 0-7-7zm0 10a3 3 0 1 1 0-6 3 3 0 0 1 0 6z"/></svg>
      <span>42 Harbour Lane,<br>Unit 3 Westfield</span>
    </div>
    <div class="contact contact--light" style="left:700px; top:420px;">
      <svg viewBox="0 0 20 20"><path d="M4 1l4 4-2 3c1 2 4 5 6 6l3-2 4 4-3 3C9 19 1 11 1 4z"/></svg>
      <span>020 555 0147</span>
    </div>
    <div class="contact contact--light" style="left:700px; top:462px;">
      <svg viewBox="0 0 20 20"><path d="M5 0h10v20H5zM7 2v13h6V2zm3 14.5a1 1 0 1 0 0 2 1 1 0 0 0 0-2z" fill-rule="evenodd"/></svg>
      <span>020 555 0183</span>
    </div>
  </div>
</body>
</html>
```